Bring me business with this creative business card

Design my new business card. I am looking for something different with an impact. People will take a look at this card & they will 1- see how different & creative I am, 2-understand what I do 3- Call me to meet me!

I make videos with a message, testimonials. I am dynamic, fun, creative & human. My new website is in construction but in the meantime you can check this old one: brightpath.ca & another one Tidebloom.com & tidebloom facebook page.
I make videos. sometimes with a cameraman, sometimes with my phone. As an ex Public Relations agent, the message is the most important thing for me. I want to make my clients shine! When they start with me they often remind me of a lamb, when I finish coaching them they are powerful like LIONS! That's why I need a powerful business card!

Target Market(s)

Entrepreneurs, solo entrepreneurs, small & medium companies & start ups. People i will meet while networking. People that need videos on their website & social Networks to get attention, to be visible. men & women. From 35 to 49 years old.
I am an ex Public relations agent. I used to send clients in traditional medias, now with videos they have more chances to be seen on google the new media. I do videos of the president, his team, his loyal clients saying how great the company is & expert videos like series so people can be seen for example every 1 st of every month with a short 2 minute video. Also with my 20 years in marketing & communications I can coach & give tips to anybody who needs it.
Target: anybody who would like my old website brightpath.ca & I also have another website but it will be off line soon: tidebloom.com could give you ideas.

Industry/Entity Type

Communications

Contact Information for Business Card

I am in Montreal,So the business cards have to be the usual size like we have in Montreal: 9 cm x 5 cm
Details:My text: Mathilde Tessier Communication coach/Chief Lion. "Creating Videos as unique as you" off: 514-555-0147 cell: 514-555-0183. tidebloom.com
mathilde@tidebloom.com logo facebook, youtube, instagram

Colors
f37122

Requirements
Must have
• Dynamic, happy. Orange. Be creative in the look but NOT the shape of the card. Easy to read. Big enough to read.
Should not have
• No funny shapes: no round, no square, just the usual. I love creative but NOT on shape.

```html
<!DOCTYPE html>
<html lang="en">
<head>
<meta charset="utf-8">
<title>Tidebloom Business Card</title>
<link href="https://fonts.googleapis.com/css2?family=Cinzel:wght@700&family=Roboto:wght@400;500&display=swap" rel="stylesheet">
<style>
  :root {
    --page: #ece7e1;
    --ink-dark: #1b1c1e;
    --paper: #f6f6f6;
    --orange: #f37122;
    --amber: #f7a21b;
    --gold: #fcc52a;
    --text-grey: #4a4a4a;
    --rule: #e9e2d8;
  }
  * { margin: 0; padding: 0; box-sizing: border-box; }
  html, body { width: 1200px; height: 960px; overflow: hidden; }
  body { background: var(--page); position: relative; font-family: "Roboto", Arial, sans-serif; }

  .card { position: absolute; overflow: hidden; box-shadow: 0 3px 8px rgba(0,0,0,.25); }

  /* Front */
  .card-front { left: 320px; top: 104px; width: 606px; height: 340px; background: var(--ink-dark); }
  .brand-mark { position: absolute; left: 242px; top: 68px; width: 120px; height: 120px; border-radius: 50%;
    background: radial-gradient(circle at 50% 45%, var(--gold), var(--amber) 55%, var(--orange)); }
  .brand-name { position: absolute; left: 0; right: 0; top: 198px; text-align: center;
    font-family: "Cinzel", "Times New Roman", serif; font-weight: 700; font-size: 36px; letter-spacing: 1px; color: var(--orange); }
  .brand-slogan { position: absolute; left: 0; right: 0; top: 240px; display: flex; justify-content: center; align-items: center; gap: 8px;
    font-size: 14px; color: var(--amber); letter-spacing: .3px; }
  .brand-slogan::before, .brand-slogan::after { content: ""; width: 30px; height: 1px; background: var(--amber); }
  .brand-promise { position: absolute; left: 0; right: 0; top: 259px; text-align: center; font-size: 14px; font-weight: 500; color: var(--orange); }
  .social-row { position: absolute; left: 168px; top: 300px; width: 270px; height: 24px; display: flex; align-items: center; gap: 4px; }
  .social-row .rule { flex: 1; height: 1px; background: linear-gradient(90deg, var(--rule), var(--orange)); }
  .social-row .rule.right { background: linear-gradient(90deg, var(--orange), var(--rule)); }
  .social-dot { width: 23px; height: 23px; border-radius: 50%; background: var(--orange); }
  .social-dot.outline { background: none; border: 1.5px solid var(--orange); }

  /* Back */
  .card-back { left: 320px; top: 493px; width: 600px; height: 342px; background: var(--paper); }
  .back-band { position: absolute; right: 0; top: 0; width: 130px; height: 100%; background: var(--ink-dark); }
  .back-art { position: absolute; left: 315px; top: 30px; width: 280px; height: 300px; border-radius: 50%;
    background: radial-gradient(circle at 50% 55%, var(--gold), var(--amber) 50%, var(--orange)); }
  .person-name { position: absolute; left: 32px; top: 24px; font-size: 23px; font-weight: 500; color: var(--orange); letter-spacing: .3px; }
  .person-role { position: absolute; left: 32px; top: 52px; font-size: 15px; line-height: 19px; color: var(--amber); }
  .contact-list { position: absolute; left: 33px; top: 243px; list-style: none; }
  .contact-list li { display: flex; align-items: center; gap: 9px; height: 19.5px; font-size: 14.5px; color: var(--text-grey); }
  .contact-list svg { width: 13px; height: 13px; fill: var(--orange); flex: none; }
</style>
</head>
<body>

<section class="card card-front">
  <div class="brand-mark"></div>
  <div class="brand-name">TIDEBLOOM</div>
  <div class="brand-slogan">1 VIDEO&nbsp; 1 MESSAGE</div>
  <div class="brand-promise">Creating Videos as unique as you</div>
  <div class="social-row">
    <span class="rule"></span>
    <span class="social-dot"></span>
    <span class="social-dot"></span>
    <span class="social-dot outline"></span>
    <span class="rule right"></span>
  </div>
</section>

<section class="card card-back">
  <div class="back-band"></div>
  <div class="back-art" role="img" aria-label="Large orange emblem area"></div>
  <div class="person-name">MATHILDE T.</div>
  <div class="person-role">COMMUNICATION COACH<br>CHIEF LION</div>
  <ul class="contact-list">
    <li><svg viewBox="0 0 16 16"><path d="M3 1l3 3-2 2c1 2.5 3.5 5 6 6l2-2 3 3-2 2C7 14 2 9 1 3z"/></svg>514-555-0147</li>
    <li><svg viewBox="0 0 16 16"><path d="M4 0h8a1 1 0 011 1v14a1 1 0 01-1 1H4a1 1 0 01-1-1V1a1 1 0 011-1zm1 2v10h6V2zm3 11a1 1 0 100 2 1 1 0 000-2z"/></svg>514-555-0183</li>
    <li><svg viewBox="0 0 16 16"><path d="M1 3h14v10H1zm1.5 1.5L8 9l5.5-4.5z"/></svg>mathilde@tidebloom.com</li>
    <li><svg viewBox="0 0 16 16"><path d="M8 1a7 7 0 100 14A7 7 0 008 1zm-1 2c-1 1-2 2-1 3s2 0 2 2-2 1-2 3l-1 2A5.5 5.5 0 017 3zm3 1c1 1 3 2 3 4l-2 1-1-2z"/></svg>www.tidebloom.com</li>
  </ul>
</section>

</body>
</html>
```